Business card for denture clinic Veltrimora

We need a new business card with our new logo. We are a denture clinic in New Zealand with our target market being 45+ years old. We would need a space on the back to write our patients next appointment on. We would space for only one appointment rather than a list. We will attach a photo showing an example of this. But of course, we would like to see your twist on this. We want it to be bold and easy to read and a good mixture of professional but modern. We have attached our logo to be used on the card.

Target Market(s)

People aged 45+ needing dentures

Industry/Entity Type

Dental

Contact Information for Business Card

We want our logo on the front and the space to write an appointment on the back. I've attached an example our our old business card showing this. We need to have the technicians details on the front.

Font styles to use
Sans Serif

Colors
0255a3
919191
fbfbfb

Requirements
Must have
• The following details:
• Liam Dorsett BDT, PGDipCDentTech Calverin
• Dental Prosthetist
• Phone numbers: 0800 47 3125
• 09 572 1394
• Email: liam@veltrimora.co.nz
• www.veltrimora.co.nz
• Address: 14 Marlow Crest Road
• Halbrook West
• Auckland 0793
Nice to have
• We would like our business cards to have more than just two colours as we want them to be more vibrant. We have uploaded an example of a business card we liked that showed this.

```html
<!DOCTYPE html>
<html lang="en">
<head>
<meta charset="utf-8">
<title>Veltrimora Business Card</title>
<link href="https://fonts.googleapis.com/css2?family=Lato:ital,wght@0,400;0,700;0,900;1,400&display=swap" rel="stylesheet">
<style>
  :root{
    --brand-blue:#0260a3;
    --brand-grey:#919191;
    --paper:#f3f3f3;
    --white:#ffffff;
    --stage:#e9e9e9;
  }
  *{box-sizing:border-box;margin:0;padding:0}
  html,body{width:1200px;height:586px;overflow:hidden;background:var(--stage);font-family:'Lato',sans-serif}
  .stage{position:relative;width:1200px;height:586px}
  .card{position:absolute;top:129px;width:501px;height:301px;overflow:hidden;box-shadow:0 8px 14px rgba(0,0,0,.18)}
  .card--back{left:61px;background:var(--paper)}
  .card--front{left:619px;background:var(--paper)}

  .band{position:absolute;left:0;width:100%;background:var(--brand-blue)}
  .stripe{position:absolute;left:0;width:100%;height:3px;background:var(--brand-blue)}

  /* back: appointment */
  .card--back .band{top:0;height:206px}
  .appt-title{position:absolute;top:37px;left:0;width:100%;text-align:center;color:var(--white);font-weight:700;font-size:13.5px;letter-spacing:4.6px}
  .appt-title span{border-bottom:1px solid var(--white);padding:0 0 3px 4px}
  .field-label{position:absolute;top:90px;color:var(--white);font-size:12.5px}
  .field-box{position:absolute;top:112px;width:204px;height:33px;background:var(--white);border-radius:4px}
  .wordmark{position:absolute;left:0;width:100%;text-align:center;color:var(--brand-blue);font-weight:900;letter-spacing:3px;text-transform:uppercase;font-size:29px}
  .tagline{position:absolute;left:0;width:100%;text-align:center;font-weight:700;letter-spacing:3.2px;text-transform:uppercase;font-size:11.5px}
  .card--back .wordmark{top:230px}
  .card--back .tagline{top:265px;color:var(--brand-blue)}

  /* front: details */
  .logo-square{position:absolute;left:226px;top:33px;width:49px;height:49px;background:var(--brand-blue);border-radius:3px}
  .card--front .wordmark{top:84px}
  .card--front .tagline{top:118px;color:var(--brand-grey)}
  .card--front .band{top:173px;height:128px}
  .identity{position:absolute;right:302px;text-align:right;color:var(--white);white-space:nowrap}
  .identity__name{top:188px;font-size:15.5px;font-weight:900}
  .identity__qual{top:210px;font-size:10.5px;font-style:italic}
  .identity__role{top:231px;font-size:11px;font-weight:700}
  .identity__address{top:253px;font-size:10.5px;line-height:14px}
  .divider{position:absolute;left:230px;top:186px;width:1px;height:104px;background:linear-gradient(rgba(255,255,255,0),rgba(255,255,255,.8),rgba(255,255,255,0))}
  .contact{position:absolute;left:256px;display:flex;align-items:center;gap:8px;color:var(--white);font-size:12px}
  .contact svg{width:17px;height:17px;flex:none}
</style>
</head>
<body>
<div class="stage">

  <section class="card card--back" aria-label="Appointment side">
    <div class="band"></div>
    <div class="appt-title"><span>Your Next Appointment</span></div>
    <div class="field-label" style="left:39px">Date:</div>
    <div class="field-box" style="left:39px"></div>
    <div class="field-label" style="left:266px">Time:</div>
    <div class="field-box" style="left:266px"></div>
    <div class="stripe" style="top:209px"></div>
    <div class="stripe" style="top:216px"></div>
    <div class="wordmark">Veltrimora</div>
    <div class="tagline">The Denture Experts</div>
  </section>

  <section class="card card--front" aria-label="Details side">
    <div class="logo-square"></div>
    <div class="wordmark">Veltrimora</div>
    <div class="tagline">The Denture Experts</div>
    <div class="stripe" style="top:160px"></div>
    <div class="stripe" style="top:167px"></div>
    <div class="band"></div>

    <div class="identity identity__name">Liam Dorsett BDT</div>
    <div class="identity identity__qual">PGDipCDentTech Calverin</div>
    <div class="identity identity__role">Dental Prosthetist</div>
    <div class="identity identity__address">14 Marlow Crest Road, Halbrook West<br>Auckland 0793</div>
    <div class="divider"></div>

    <div class="contact" style="top:190px">
      <svg viewBox="0 0 20 20" aria-hidden="true"><circle cx="10" cy="10" r="10" fill="#fff"/><path d="M5 8c0-2 2-3 5-3s5 1 5 3l-2 1-1-1.5H8L7 9zM7 10h6l1.5 4h-9z" fill="#0260a3"/></svg>
      <span>0800 47 3125</span>
    </div>
    <div class="contact" style="top:215px">
      <svg viewBox="0 0 20 20" aria-hidden="true"><circle cx="10" cy="10" r="10" fill="#fff"/><path d="M5 8c0-2 2-3 5-3s5 1 5 3l-2 1-1-1.5H8L7 9zM7 10h6l1.5 4h-9z" fill="#0260a3"/></svg>
      <span>09 572 1394</span>
    </div>
    <div class="contact" style="top:240px">
      <svg viewBox="0 0 20 20" aria-hidden="true"><circle cx="10" cy="10" r="10" fill="#fff"/><rect x="5" y="6.5" width="10" height="7" fill="#0260a3"/><path d="M5 6.5l5 4 5-4" fill="none" stroke="#fff" stroke-width="1"/></svg>
      <span>liam@veltrimora.co.nz</span>
    </div>
    <div class="contact" style="top:265px">
      <svg viewBox="0 0 20 20" aria-hidden="true"><circle cx="10" cy="10" r="10" fill="#fff"/><circle cx="10" cy="10" r="5" fill="none" stroke="#0260a3" stroke-width="1.3"/><path d="M5 10h10M10 5c-2.5 3-2.5 7 0 10M10 5c2.5 3 2.5 7 0 10" fill="none" stroke="#0260a3" stroke-width="1"/></svg>
      <span>www.veltrimora.co.nz</span>
    </div>
  </section>

</div>
</body>
</html>
```